Public Speaking Parable Fiction Book Cover

I have written a parable story to teach public speaking concepts. The main character, Marcus's twin sister, Orla, has just died. He goes on a cruise ship where he meets a number of performers who teach him life lessons and public speaking concepts. The themes of the story are memory, healing, magic, and communication.

I would like the cover to be a two-sided paperback cover that can be uploaded to Brindle for self-publishing. My idea is to have Marcus on the deck of the ship looking out to sea. There, he can see a silhouette of his sister, and a compass to signify trying to find direction. The colour scheme is purple and blue. I've attached some QuillBot9 mock-ups of the cover, Marcus and Orla to give you an idea.

I'd like the title of the book "The Orator's Ballad" to be at the top of the page, and the author's name "Colin Farrowby, MSc" to be at the bottom.

Target Market(s)

Professionals looking to improve public speaking skills but burned out with reading non-fiction

Font styles to use
Script

Colors

Designer to choose colors to be used in the design.

Requirements
Must have
• Front and Back cover design compatible with Brindle Self-publishing
Should not have
• Cartoony graphics

```html
<!DOCTYPE html>
<html lang="en">
<head>
<meta charset="utf-8">
<title>The Orator's Ballad – Paperback Wrap Cover</title>
<link rel="stylesheet" href="https://fonts.googleapis.com/css2?family=Playfair+Display:wght@500&family=Pinyon+Script&family=Roboto+Slab:wght@300&display=swap">
<style>
  :root {
    --page: #ffffff;
    --sky-top: #0b2a6f;
    --sky-mid: #3a3f9e;
    --glow: #b98fd8;
    --sunset: #d9a3a0;
    --sea: #1f2c6e;
    --deck: #25234f;
    --deck-deep: #1a1940;
    --ink-light: #f2eefc;
    --title-blue-a: #1f6fc4;
    --title-blue-b: #a8d6f6;
    --title-white: #ffffff;
    --title-lilac: #b7a8ec;
    --script-blue: #4e86d6;
    --placeholder: #8f91a3;
  }
  * { box-sizing: border-box; margin: 0; padding: 0; }
  html, body { width: 1200px; height: 872px; overflow: hidden; background: var(--page); }

  .wrap-cover {
    position: absolute; left: 30px; top: 33px;
    width: 1140px; height: 805px; overflow: hidden;
    box-shadow: 0 0 18px rgba(0,0,0,.35);
  }
  .cover-scene {
    position: absolute; inset: 0;
    background:
      radial-gradient(ellipse 90px 120px at 755px 345px, rgba(255,240,255,.9), rgba(200,150,230,.35) 45%, transparent 75%),
      radial-gradient(ellipse 260px 70px at 140px 355px, rgba(230,170,150,.55), transparent 80%),
      linear-gradient(180deg, var(--sky-top) 0%, var(--sky-mid) 32%, var(--glow) 46%, var(--sea) 48.5%, var(--sea) 56%, var(--deck) 64%, var(--deck-deep) 100%);
  }
  .cover-scene::after {
    content: ""; position: absolute; left: 880px; top: 115px; width: 250px; height: 690px;
    background: linear-gradient(180deg, rgba(14,18,48,.85), rgba(22,26,64,.9));
    border-radius: 45% 45% 0 0 / 12% 12% 0 0;
  }

  .title-the, .title-main, .title-script { display: block; text-align: center; -webkit-background-clip: text; background-clip: text; color: transparent; }
  .title-the, .title-main { font-family: "Playfair Display", serif; font-weight: 500; line-height: .85; letter-spacing: -0.04em; }
  .title-the { background-image: linear-gradient(180deg, var(--title-blue-a), var(--title-blue-b) 55%, var(--title-blue-a)); }
  .title-main { background-image: linear-gradient(180deg, var(--title-white) 30%, var(--title-lilac)); }
  .title-script { font-family: "Pinyon Script", cursive; line-height: 1; background-image: linear-gradient(180deg, var(--script-blue), var(--title-white) 70%, var(--title-lilac)); }

  .back-title { position: absolute; left: 110px; top: 84px; width: 320px; }
  .back-title .title-the { font-size: 60px; }
  .back-title .title-main { font-size: 62px; margin-top: 4px; }
  .back-title .title-script { font-size: 92px; margin-top: -4px; }

  .blurb {
    position: absolute; left: 34px; width: 470px;
    font-family: "Roboto Slab", serif; font-weight: 300; font-size: 15px; line-height: 20.7px;
    letter-spacing: .06em; color: var(--ink-light);
  }
  .blurb-1 { top: 332px; }
  .blurb-2 { top: 447px; }
  .blurb-3 { top: 587px; left: 165px; width: 340px; }
  .barcode-space { position: absolute; left: 34px; top: 591px; width: 117px; height: 116px; border-radius: 8px; background: var(--placeholder); opacity: .9; }

  .spine { position: absolute; left: 544px; top: 46px; width: 62px; height: 740px; writing-mode: vertical-rl; }
  .spine-title { display: flex; align-items: baseline; gap: 6px; }
  .spine-title .title-main { font-size: 46px; letter-spacing: -0.05em; }
  .spine-title .title-script { font-size: 50px; }
  .spine-author {
    position: absolute; top: 545px; right: 6px;
    font-family: "Roboto Slab", serif; font-weight: 300; font-size: 19px; line-height: 28px;
    letter-spacing: .2em; color: var(--ink-light);
  }

  .front-author {
    position: absolute; left: 640px; top: 64px; width: 480px; text-align: center;
    font-family: "Roboto Slab", serif; font-weight: 300; font-size: 25px; letter-spacing: .2em;
    color: var(--ink-light);
  }
  .front-title { position: absolute; left: 630px; top: 420px; width: 500px; }
  .front-title .title-the { font-size: 92px; width: 210px; }
  .front-title .title-main { font-size: 92px; margin-top: 10px; }
  .front-title .title-script { font-size: 150px; margin-top: -8px; }
</style>
</head>
<body>
  <div class="wrap-cover">
    <div class="cover-scene" role="img" aria-label="Photograph: twilight sea from a cruise ship deck with railing; a bearded man in a dark jacket holds an open compass and looks toward the silhouette of a woman standing in the sunset glow on the water"></div>

    <section class="back-cover">
      <h2 class="back-title">
        <span class="title-the">THE</span>
        <span class="title-main">ORATOR’S</span>
        <span class="title-script">Ballad</span>
      </h2>
      <p class="blurb blurb-1">Lorem ipsum dolor sit amet, consectetur adipiscing elit, sed do eiusmod tempor incididunt ut labore et dolore magna aliqua. Quis ipsum suspendisse ultrices gravida. Risus commodo viverra maecenas accumsan lacus vel facilisis.</p>
      <p class="blurb blurb-2">Lorem ipsum dolor sit amet, consectetur adipiscing elit, sed do eiusmod tempor incididunt ut labore et dolore magna aliqua.consectetur adipiscing elit, sed do eiusmod tempor incididunt ut labore et dolore magna aliqua. Quis ipsum suspendisse ultrices gravida. Risus commodo viverra maecenas accumsan lacus vel</p>
      <div class="barcode-space"></div>
      <p class="blurb blurb-3">Lorem ipsum dolor sit amet, consectetur adipiscing elit, sed do eiusmod tempor incididunt ut labore et dolore magna aliqua. Quis ipsum suspendisse ultrices gravida. Risus commodo viverra maece-nas accumsan lacus vel facilisis.</p>
    </section>

    <section class="spine">
      <h2 class="spine-title">
        <span class="title-main">THE ORATOR’S</span>
        <span class="title-script">Ballad</span>
      </h2>
      <p class="spine-author">Colin<br>Farrowby, MSc</p>
    </section>

    <section class="front-cover">
      <p class="front-author">Colin Farrowby, MSc</p>
      <h1 class="front-title">
        <span class="title-the">THE</span>
        <span class="title-main">ORATOR’S</span>
        <span class="title-script">Ballad</span>
      </h1>
    </section>
  </div>
</body>
</html>
```